Brochure for a website accessibility report

This brochure is related to a report that www.qelvantrix.org sell. The report shows the results of an automated audit of a websites accessibility. It shows details of issues found with screen shots, examples of code and provides remediation advice.

The brochure will be a pdf 8.5 inches by 11 inches. It can be anywhere from 6 to 10 pages.

The FlintVue™ name itself should be “Bree Serif” font. The fonts, styles, colors and sizes are up to you.

The images used and logo of the Office of Digital Reachworks and K7P logo are upload

We highlighted in blue page extracts from the report we sell. Do not use the blue highlight, it is merely there to show you where the specific examples of the report we sell are vs the other content in the report. The areas in blue which show the content from the actual report should be shown as an extract of the actual page of the report. You have flexibility to change the layout and the way the content look.

The red square callouts over the blue content are callouts that describe the specific page extracts. We used it as a red callout only so that you would be able to see it. You should change the specific location, look and feel of the callout to be appropriate

Target Market(s)

Marketing and Technical people

Industry/Entity Type

Information Technology

Font styles to use
Sans Serif

Colors

Designer to choose colors to be used in the design.

Requirements
Should not have
• wheelchairs, images of blind people

```html
<!DOCTYPE html>
<html lang="en">
<head>
<meta charset="utf-8">
<title>FlintVue™ Report — Scripting</title>
<link rel="stylesheet" href="https://fonts.googleapis.com/css2?family=Bree+Serif&family=Roboto:wght@400;500&display=swap">
<style>
  :root{
    --page:#ffffff;
    --navy:#0e3a5c;
    --panel:#2f87c1;
    --yellow:#f6cb3e;
    --accent:#f3d03c;
    --link:#55d6d2;
    --text:#ffffff;
    --ink:#0e3a5c;
    --code-bg:#e9e9e9;
    --code-ink:#333333;
  }
  *{box-sizing:border-box;margin:0;padding:0}
  html,body{width:927px;height:1200px;overflow:hidden;background:var(--page)}
  body{position:relative;font-family:"Roboto",sans-serif;color:var(--text)}
  .page-card{position:absolute;left:53px;top:52px;width:823px;height:1095px;background:var(--navy);border-radius:72px}
  .abs{position:absolute}
  .section-title{left:102px;top:74px;font-family:"Bree Serif",serif;font-size:35px;color:var(--yellow)}
  .intro{left:102px;top:136px;width:724px;font-size:16px;line-height:20px;font-weight:400}
  .rules{left:102px;top:208px;width:690px;list-style:none;font-size:16px;line-height:20px}
  .rules li{position:relative;padding-left:32px;margin-bottom:12px;text-align:justify}
  .rules li::before{content:"";position:absolute;left:3px;top:7px;width:6px;height:6px;background:var(--link)}
  .issue{left:102px;top:345px;width:730px;font-size:16px;line-height:25.5px}
  .label{font-weight:500}
  .hl{color:var(--accent)}
  .advice{left:102px;top:491px;width:730px;font-size:16px;line-height:25.5px}
  .reading{left:102px;top:589px;font-size:16px;line-height:20.5px}
  .reading a{display:block;margin-left:51px;color:var(--link);text-decoration:none}
  .callout{position:absolute;background:var(--yellow);border-radius:20px;color:var(--ink);font-size:14px;line-height:17.5px;text-transform:uppercase}
  .callout-classification{left:534px;top:25px;width:308px;height:92px;padding:30px 0 0 32px}
  .callout-examples{left:353px;top:589px;width:489px;height:93px;padding:30px 0 0 31px;font-size:13.6px}
  .pointer{position:absolute;overflow:visible}
  .example-panel{position:absolute;left:84px;top:699px;width:759px;height:412px;background:var(--panel);border-radius:22px}
  .example-head{left:104px;top:713px;font-size:17px;font-weight:500;letter-spacing:.2px}
  .example-head .url{font-weight:400;margin-left:8px}
  .specific{left:106px;top:756px;width:380px;font-size:16px;line-height:22.6px}
  .specific h3,.snippet-title{font-size:17px;font-weight:500;margin-bottom:8px;letter-spacing:.2px}
  .serif-code{font-family:"Bree Serif",serif;color:var(--accent);font-size:15.5px}
  .snippet-title{left:106px;top:946px}
  .code-box{left:104px;top:978px;width:384px;height:30px;background:var(--code-bg);color:var(--code-ink);font-family:"Bree Serif",serif;font-size:13px;line-height:30px;padding-left:12px}
  .screenshot{left:509px;top:758px;width:310px;height:329px;border:3px solid #ffffff;background:linear-gradient(180deg,#1d3e62 0 28%,#f4f1ec 28% 100%)}
</style>
</head>
<body>
  <div class="page-card"></div>

  <h1 class="abs section-title">Scripting</h1>

  <div class="callout callout-classification">Detailed explanations of the classification to be fixed</div>
  <svg class="pointer" style="left:440px;top:55px" width="100" height="45" viewBox="0 0 100 45" aria-hidden="true">
    <polygon points="2,27 96,0 96,45" fill="var(--yellow)"/>
  </svg>

  <p class="abs intro">Pages that include one of the listed scripts should be checked to make sure they're still usable without the script. All Webpage content should be accessible without the use of JavaScript. (even if it takes the user additional or alternative steps.)</p>

  <ul class="abs rules">
    <li>Each script should be checked to make sure it doesn't cause unexpected changes in context and doesn't impose timing burdens on the user; such as automatic refreshing or changes of content. The user must have the ability to ignore, pause or somehow control such timed responses so they do not adversely affect the visitor reading experience.</li>
    <li>Scripting should not be a requirement to access essential Webpage content.</li>
  </ul>

  <div class="abs issue">
    <p class="label">ISSUE: <span class="hl">CLICK EVENT (PRIORITY 3)</span></p>
    <p>OnClick Events may be inaccessible.</p>
    <p>If clicking on the element associated with the OnClick event handler triggers a function or performs some other action, developers should ensure that the context makes that fact clear to all users.</p>
    <p>Issue is relevant to checkpoints: &nbsp;&nbsp;&nbsp;<span class="hl">2.1.1 (A)</span>.</p>
  </div>

  <div class="abs advice">
    <p class="label">General Remediation Advice:</p>
    <p>Review the surrounding area/content of the clickable element and ensure that sufficient and accessible instruction text is provided with regard to the element.</p>
  </div>

  <div class="abs reading">
    <p class="label">Suggested Reading:</p>
    <a href="#">Keyboard Accessible</a>
    <a href="#">Keyboard (No Exception)</a>
  </div>

  <div class="example-panel"></div>

  <div class="callout callout-examples">Multiple example including the URL of the issue show developers' different examples of the issue described</div>
  <svg class="pointer" style="left:380px;top:680px" width="50" height="33" viewBox="0 0 50 33" aria-hidden="true">
    <polygon points="0,0 44,0 24,33" fill="var(--yellow)"/>
  </svg>

  <p class="abs example-head">EXAMPLE 1 OF 3: <span class="url">HTTP://WWW.GLOBALGOALSHUB.ORG/TARGETS/</span></p>

  <div class="abs specific">
    <h3>SPECIFIC ISSUES:</h3>
    <p>Confirm that information describing the purpose of '<span class="serif-code">onClick</span>' and '<span class="serif-code">onKeyPress</span>' events is available and adjacent to the element that activates the event.<br>Found<br><span class="serif-code">'&lt;A&gt; Tag id='folder01' &nbsp;onclick='showHide('folder01'); return false;'</span></p>
  </div>

  <p class="abs snippet-title">CODE SNIPPET</p>
  <div class="abs code-box">&lt;h5&gt;Assembly Secretariat staff&lt;/h5&gt;</div>

  <div class="abs screenshot" role="img" aria-label="Screenshot of the audited web page showing its header banner, news column and a grid of goal tiles"></div>
</body>
</html>
```